Coastal Learner Bureau business cards

Australian company about to start offering its services. We recruit international students to come to study English, vocational education and postgraduate courses in Australia. We help them find the institution and select the right city they want to come to Australia. We are a young, online oriented and supportive agency. Our clients are between 18 and 35 years old, mainly University students, young professionals or people with work experience. We provide much more information that any other agency offer. We administrate a Facebook group with more than 11.000 members that daily ask questions about general information when coming to Australia, while they are here and even after they leave the country

Target Market(s)

International students from South America, Central America and Europe

Industry/Entity Type

Student

Contact Information for Business Card

Tomas Bilbrea
Managing Director
tomas@kelvarin.com.au
www.kelvoria.com.au
+61 491058264
Melbourne, Australia

Font styles to use
Serif
Sans Serif

Colors

Designer to choose colors to be used in the design.

Requirements
Must have
• Horizontal design
• Standard business card size and shape. If font uses green or yellow colours, they will have to match the ones from the logo
Nice to have
• UPDATE: Use the contents of the green image to design one of the card sides. Use our logo in the background of that side as watermark.
• Passport image, or immigration stamps. A picture of the Yarra River (from Melbourne) would be cool as well.
Should not have
• Non-standard business card size and shape
• Not black as the background colour of any sides as we are not a VIP agency or a hight class service. We are orientes to young people and they like colours, pictures, something attractive.
• Vertical design
• NO YELLOW or BLACK AS THE BACKGROUND COLOUR OF ANY SIDE OF THE BIZ CARD

```html
<!DOCTYPE html>
<html lang="en">
<head>
<meta charset="utf-8">
<title>Coastal Learner Bureau business cards</title>
<link href="https://fonts.googleapis.com/css2?family=Roboto:wght@400;500;700&family=Roboto+Condensed:wght@700&display=swap" rel="stylesheet">
<style>
  :root {
    --green: #115c3d;
    --gold: #dcb30f;
    --paper: #f3f3f3;
    --ink: #444444;
    --backdrop: #e4e4e4;
    --white: #ffffff;
  }
  html, body {
    margin: 0;
    padding: 0;
    width: 1200px;
    height: 960px;
    overflow: hidden;
    background: var(--backdrop);
    font-family: "Roboto", Arial, sans-serif;
  }
  .card {
    position: absolute;
    width: 600px;
    height: 343px;
    overflow: hidden;
  }
  .card-front { left: 314px; top: 113px; background: var(--paper); }
  .card-back { left: 311px; top: 472px; background: var(--green); }

  .brand-name {
    position: absolute;
    font-family: "Roboto", Arial, sans-serif;
    font-weight: 700;
    letter-spacing: 0.5px;
    white-space: nowrap;
  }
  .card-front .brand-name {
    right: 38px;
    top: 70px;
    font-size: 40px;
    color: var(--green);
  }
  .card-back .brand-name {
    left: 0;
    right: 0;
    top: 130px;
    text-align: center;
    font-size: 58px;
    color: var(--white);
  }

  .holder { position: absolute; left: 45px; top: 180px; }
  .holder-name {
    margin: 0;
    font-family: "Roboto Condensed", Arial, sans-serif;
    font-weight: 700;
    font-size: 22px;
    color: var(--green);
    letter-spacing: 0.3px;
  }
  .holder-role {
    margin: 2px 0 0;
    font-size: 15px;
    font-weight: 500;
    color: var(--gold);
  }

  .contact {
    position: absolute;
    right: 37px;
    top: 227px;
    margin: 0;
    padding: 0;
    list-style: none;
    text-align: right;
    font-size: 14px;
    color: var(--ink);
    line-height: 19.5px;
  }
  .contact li { display: flex; justify-content: flex-end; align-items: center; gap: 6px; }
  .contact .icon { width: 13px; height: 13px; fill: var(--green); }
  .contact .plain { padding-right: 0; }

  .wave { position: absolute; left: 0; top: 0; }
  .website {
    position: absolute;
    right: 48px;
    top: 317px;
    font-size: 14px;
    color: var(--white);
  }

  .tagline {
    position: absolute;
    left: 64px;
    right: 64px;
    top: 300px;
    display: flex;
    align-items: center;
    gap: 4px;
    color: var(--white);
    font-size: 14px;
  }
  .tagline .rule { flex: 1; height: 1px; }
  .tagline .rule-left { background: linear-gradient(to right, rgba(255,255,255,0), rgba(255,255,255,0.85)); }
  .tagline .rule-right { background: linear-gradient(to left, rgba(255,255,255,0), rgba(255,255,255,0.85)); }
</style>
</head>
<body>

<section class="card card-front" aria-label="Business card front">
  <div class="brand-name">Kelvoria</div>

  <div class="holder">
    <p class="holder-name">TOMAS BILBREA</p>
    <p class="holder-role">Managing Director</p>
  </div>

  <ul class="contact">
    <li>+61 491058264
      <svg class="icon" viewBox="0 0 24 24" aria-hidden="true"><path d="M6.6 10.8c1.4 2.8 3.8 5.1 6.6 6.6l2.2-2.2c.3-.3.7-.4 1-.2 1.1.4 2.3.6 3.6.6.6 0 1 .4 1 1V20c0 .6-.4 1-1 1C10.6 21 3 13.4 3 4c0-.6.4-1 1-1h3.5c.6 0 1 .4 1 1 0 1.3.2 2.5.6 3.6.1.3 0 .7-.2 1L6.6 10.8z"/></svg>
    </li>
    <li>tomas@kelvarin.com.au
      <svg class="icon" viewBox="0 0 24 24" aria-hidden="true"><path d="M2 5h20v14H2z M3.5 6.5 12 12.5l8.5-6" fill="var(--green)" stroke="var(--paper)" stroke-width="1.6"/></svg>
    </li>
    <li class="plain">Melbourne, Australia</li>
  </ul>

  <svg class="wave" width="600" height="343" viewBox="0 0 600 343" aria-hidden="true">
    <path d="M0,280 C80,310 180,328 300,314 C420,300 520,294 600,322 L600,343 L0,343Z" fill="var(--gold)"/>
    <path d="M0,309 C100,332 200,330 300,318 C420,304 520,300 600,326 L600,343 L0,343Z" fill="var(--white)"/>
    <path d="M0,312 C100,335 200,333 300,321 C420,307 520,303 600,329 L600,343 L0,343Z" fill="var(--green)"/>
  </svg>
  <div class="website">www.kelvoria.com.au</div>
</section>

<section class="card card-back" aria-label="Business card back">
  <div class="brand-name">Kelvoria</div>
  <div class="tagline">
    <span class="rule rule-left"></span>
    <span>Hacemos más por ti!</span>
    <span class="rule rule-right"></span>
  </div>
</section>

</body>
</html>
```